Private Investigative Business Needs Brochure Design

I need a highly professional and contemporary brochure for a new private investigative business I own. I am a retired detective with 35 years of investigative experience. I am looking to obtain all types of clients, with a primary focus on law firms, attorneys, insurance companies, businesses, schools, elderly, families and individuals . I have a web site to use to get more information on what I am doing and seeking, Thanks very much! Much of the content I will use can come from my website www.BrantonPI.com. I may want to add or change a pic or two once I see the results from the design experts. Hope that is ok
Updates

I am sorry for the late changes but most of them are simply cut and paste from the below information. I reworded some of the information I currently have on my website. If possible I am seeking a brochure design that includes some of the pics I already posted along with the below information. Please let me know if you have any questions and thank you to all for your great design work. My spacing and font is not correct and needs your expertise as well.I do appreciate it!• Branton Investigative Services, LLC President, Cal Branton is a former Captain with the Oakridge State Patrol and Chief of Detectives with a county prosecutor’s office. Cal has 35 years of investigative experience. • No, we don’t offer bodyguards, drones, or conduct polygraphs, but the investigative services we offer you we are among the very best at conducting.• Our experience has taught us how to operate in tightly scripted environments, paying strict attention to applicable laws. We conduct the finest private investigations without invading anyone’s privacy, and we meticulously avoid steps-even if legal- that may not be in your best interest. Our results will stand up to the harshest of scrutiny by judges, juries, attorneys, the media and the public. • Branton Investigative Services, LLC specializes in helping litigators-across all areas of practice-succeed in depositions, trials, and negotiations. We are skilled at finding admissible evidence that is often hidden through various means or reluctant witnesses.Cal Branton is President of Branton Investigative Services, LLC. He is a former executive officer with 35 years of law enforcement and investigative experience. He obtained the rank of Captain with the Oakridge State Patrol (retired) and Chief of Detectives with the Fenwick County Prosecutor’s Office during his extensive law enforcement career.His experience with the Oakridge State Patrol included assignment to and supervision of numerous investigative units that included:• Special Projects/Auto Unit • Official Corruption Unit • High Technology Crimes and Investigative Support Unit (Unit Leader) • Special Investigations and Services Bureau (Bureau Chief)• Polygraph Unit • TRAK Unit (homicide tracking) • Special Investigations Unit (Background Investigations) • Brookvale Arena Grounds Unit • Alcohol Beverage Control Unit • Internal Affairs and Investigations Bureau• Office of Professional Standards (Bureau Chief) Cal has a vast amount of experience successfully investigating high profile criminal cases that included, homicides, aggravated assaults, missing persons, sexual assaults, white collar crimes, political corruption, official misconduct, Internet frauds, corporate frauds, identity thefts, burglaries, bank robberies, manufacturer/distribution of child pornography, conspiracy and much more. In addition, he was instrumental in the creation and oversight of numerous highly successful multi agency investigative task forces that included: • Oakridge State Patrol Statewide Computer Crimes Task Force • Oakridge State Patrol Cyber Terrorism Task Force • Online Youth Exploitation Response Group (OYRG)• Oakridge State Patrol Upper District Corruption Task Force Upon retirement from the Oakridge State Patrol Cal continued his law enforcement and investigative career as a detective assigned to the Major Crimes Unit for the Fenwick County Prosecutor’s Office. Within two years Cal was promoted from the rank of detective to the Chief of Detectives, a position he held for several years. He had oversight over all major crimes within the county, while working with municipal, county, state, and federal law enforcement agencies. As Chief of Detectives he was instrumental in the supervision of a multi-agency task force that successfully investigated and arrested a serial killer responsible for the murder and attempted murder of numerous women along the East Coast. He helped implement and supervise their first county Computer Crimes Unit, Intelligence Unit and Office of Professional Standards Units. He also oversaw the counties Serious Crash Review Squad (SCRS) and created the FCPO School Safety County Task Force. Cal is a graduate of Tolland Valley Community College and Ashgrove Pemberly University, obtaining an Associate’s Degree in Criminal Justice and a Bachelor’s Degree in Business Administration. He is also a graduate of Crestmoor University, Institute for Law Enforcement Leadership. Branton Investigative Services, LLC has extensive investigative and analytical resources available to assist with the most complex of civil investigations. Our investigative staff includes former detectives with decades of experience with the Oakridge State Patrol. In addition, we have highly skilled intelligence analysts available to assist us with investigations and your needs. We welcome any questions you may have about Branton Investigative Services, LLC and will gladly provide references. We will work tirelessly to get the job done for you, always in an ethical, legal and professional way. We are confident that if you use Branton Investigative Services, LLC one time, you will use us every time!www.BrantonPI.com (4) Please cut and paste the below under Attorney ServicesHurley Investigative Services, LLC specializes in assessing the validity of civil litigation cases, particularly when you need to determine the merit and veracity of your client’s claims. With 35 years of experience investigating criminal and civil cases we can save you significant money, time and resources throughout the litigation process, especially when you need the best factual information available prior to setting in motion a full scale litigation. Cal Branton has conducted thousands of interviews of witnesses, victims, defendants and complainants. Cal’s investigative experience enables him to be able to conduct professional, ethical, and affordable investigations for litigation cases that include: Motor Vehicle Accidents, Wrongful Deaths, Premises Liability, Nursing Home and Elder Abuse, Civil Rights, Corporate Fraud and more. He will always represent your firm, business and you in the highest of standards and always with your best interests in mind. (5) Please cut and paste the below under Corporate Fraud InvestigationsDuring the past few years we have seen a dramatic increase in the types and volume of corporate fraud committed. Corporate fraud can be committed by employees from part-time to high level management and CEO’s of major corporations. Corporate fraud can occur in any type of business, from a small family owned one to a major corporation. If you have been the victim of corporate fraud you know the significant impact it can have on your business, finances and employee morale. Companies victimized by fraud often times find themselves exposed to unwanted publicity and media coverage that can cause irrefutable damage. Cal Branton, President of Branton Investigative Services, LLC has an extensive background investigating corporate and public sector fraud, corruption, theft and embezzlement cases. We know how to operate in tightly scripted environments, paying strict attention to the law, internal policies and procedures, without bringing unwanted attention to you. With decades of investigative experience comes the ability to prepare reports that are professional, meticulously written, factually correct and understandable. Our reports and testimony withstand the scrutiny of the judges, juries, attorneys, media, individuals and the test of time. In addition, Branton Investigative Services, LLC offers consultations on how to improve retail security, reduce shrinkage from theft and implement policies and procedures to limit potential litigation. If you believe you may be the victim of corporate fraud we can perform a critical and independent assessment of the validity and strength of the evidence, culminating in a detailed exhaustive report of findings. (6) Please cut and paste the below under Accidental and Personal Injury ReconstructionHurley Investigative Services, LLC conducts thorough accident reconstruction investigations to determine the cause of the accident so you can make an informed decision. We work with attorneys, adjusters, insurance companies, and individuals involved in all types of accidents. As an independent investigator it is our duty to analyze the cause of the accident so that liability and/or financial responsibility can be resolved. It is very likely that during your lifetime you or a family member will be involved in some type of accident. You may be required to defend your actions, provide a deposition to insurance companies or become a litigant as a result of the accident not being your fault. The best decision is to do it with the assistance of Branton Investigative Services, LLC.(7) Please cut and paste the below under Background Investigations” (change checks to investigations)Branton Investigative Services, LLC provides in-depth background investigations on individuals including: pre- employment, nanny, caretaker for the elderly and more. We focus on attention to detail and thoroughness, while always conducting our investigations in a legal and ethical manner. Our comprehensive background investigation and detailed report gives you understandable, information and intelligence that helps you make the most informed decision. We utilize on-line sources, open sources, proprietary databases and information developed through interviewing and intelligence seeking the best assessment of the indivuduals reputation with your best interest always a priority. Added Thursday, April 9, 2015

Target Market(s)

Law firms, attorneys, insurance companies, businesses, education, elderly and individuals

Industry/Entity Type

Detective

Font styles to use
Sans Serif
Decorative
Script

Colors
3277b5
ffffff
33a6d7
ec1f27
85cae6
fbf289
cadf82
d3a5cc

Requirements
Must have
• Highly professional appearance, contemporary coloring, pic's that I included. In addition it is my background (bio) that is a major marketing tool that I would like placed early on.
Nice to have
• Something out of the box, primary target is attorneys and law firms
Should not have
• any typical private detective pictures

```html
<!DOCTYPE html>
<html lang="en">
<head>
<meta charset="utf-8">
<title>Branton Investigative Services – Trifold Brochure</title>
<link href="https://fonts.googleapis.com/css2?family=Roboto:wght@400;500;700;900&display=swap" rel="stylesheet">
<style>
  :root{
    --navy:#1d4f8c;
    --blue:#3277b5;
    --sky:#33a6d7;
    --ice:#85cae6;
    --lime:#cadf82;
    --lime-deep:#9cc25a;
    --paper:#ffffff;
    --paper-shade:#e4e7ea;
    --ink:#1f2329;
    --stage:#eceff2;
  }
  *{box-sizing:border-box;margin:0;padding:0}
  html,body{width:1200px;height:1000px;overflow:hidden;background:var(--stage);font-family:"Roboto",Arial,sans-serif}
  .brochure{position:absolute;left:30px;top:60px;width:1140px;height:880px;background:linear-gradient(180deg,var(--paper) 0%,var(--paper-shade) 100%);overflow:hidden;box-shadow:0 6px 24px rgba(0,0,0,.18)}
  .wave{position:absolute;inset:0;width:1140px;height:880px}
  .fold{position:absolute;top:0;width:1px;height:880px;background:rgba(0,0,0,.12)}
  .fold--one{left:380px}.fold--two{left:760px}

  .brand{position:absolute;left:22px;top:18px;display:flex;align-items:center;gap:12px}
  .brand__dot{width:54px;height:54px;border-radius:50%;background:var(--blue)}
  .brand__name{font-weight:700;font-size:22px;line-height:1.1;color:var(--navy)}
  .brand__tagline{position:absolute;left:22px;top:86px;font-size:14px;font-weight:700;color:var(--navy);border-top:3px solid var(--sky);padding-top:4px;width:300px}

  .art{position:absolute}
  .art--collage{left:0;top:135px;width:380px;height:200px;background:linear-gradient(135deg,#bfe6ee 0%,#59b8cc 45%,#e9f3f7 75%,#c9d8e6 100%)}
  .art--fraud{left:380px;top:165px;width:150px;height:170px;background:radial-gradient(circle at 50% 45%,#7fcf7a 0%,#2f7a37 55%,#123a1c 100%)}
  .art--binoculars{left:400px;top:62px;width:170px;height:90px;border-radius:45px;background:radial-gradient(circle at 30% 50%,#5aa6f0 0%,#1c3e86 40%,#222 70%)}
  .art--scales{left:545px;top:150px;width:195px;height:180px;background:radial-gradient(ellipse at 50% 55%,#f1d27b 0%,#c79a3a 45%,rgba(50,119,181,0) 72%)}
  .art--gavel{left:22px;top:550px;width:120px;height:90px;background:radial-gradient(ellipse at 50% 50%,#e8c46a 0%,#a97a26 55%,rgba(255,255,255,0) 75%)}

  .intro{position:absolute;left:22px;top:345px;width:340px;font-size:15.5px;line-height:1.32;color:var(--ink)}
  .intro strong{font-weight:700}

  .badge{position:absolute;border-radius:50%;border:5px solid var(--lime);background:radial-gradient(circle at 45% 40%,#f4f6f8 0%,#b9c3cc 100%);display:flex;align-items:center;justify-content:center;text-align:center;color:#fff;font-weight:700;line-height:1.05;text-shadow:0 0 3px #123,0 0 6px #123}
  .badge--contact{left:208px;top:590px;width:106px;height:106px;font-size:22px}
  .badge--services{left:568px;top:318px;width:124px;height:124px;font-size:25px}
  .badge--experience{left:800px;top:288px;width:122px;height:122px;font-size:20px}

  .tab{position:absolute;height:20px;border-radius:4px;background:linear-gradient(180deg,#f2f8e4,#d8ebb0);border:2px solid var(--lime-deep)}
  .tab--contact{left:190px;top:565px;width:28px;transform:rotate(40deg)}
  .tab--services{left:420px;top:372px;width:150px}
  .tab--services-r{left:1000px;top:320px;width:0}
  .tab--experience{left:926px;top:322px;width:188px}
  .tab--about{left:556px;top:72px;width:180px}

  .contact{position:absolute;left:38px;top:710px;color:var(--paper);font-size:13.5px;line-height:1.3}
  .contact__phone{font-size:18px;margin-bottom:2px}

  .services{position:absolute;left:400px;top:458px;width:352px;list-style:none;color:var(--paper);font-size:15px;line-height:1.15;text-transform:uppercase}
  .services li{display:flex;gap:7px;margin-bottom:5.5px}
  .services li.indent{padding-left:22px}
  .tick{flex:none;width:14px;height:14px;margin-top:1px}

  .about{position:absolute;left:780px;top:20px;width:345px;color:var(--paper);font-size:15.5px;line-height:1.3}
  .about__spacer{float:left;width:130px;height:128px;shape-outside:circle(50%);margin-right:6px}
  .badge--about{left:790px;top:30px;width:112px;height:112px;font-size:24px}

  .experience{position:absolute;left:790px;top:435px;width:335px;list-style:none;color:var(--paper);font-size:15px;line-height:1.18}
  .experience li{display:flex;gap:12px;margin-bottom:9px}
  .dot{flex:none;width:8px;height:8px;border-radius:50%;background:var(--ice);margin-top:6px}
  .more{position:absolute;left:790px;top:822px;width:335px;text-align:center;color:var(--paper);font-size:19px;letter-spacing:.5px}
  .more span{color:var(--ice)}
</style>
</head>
<body>
<main class="brochure">
  <svg class="wave" viewBox="0 0 1140 880" aria-hidden="true">
    <defs>
      <linearGradient id="blueField" x1="0" y1="0" x2="1" y2="1">
        <stop offset="0" stop-color="#3a86c8"/>
        <stop offset="0.55" stop-color="#3277b5"/>
        <stop offset="1" stop-color="#1d4f8c"/>
      </linearGradient>
    </defs>
    <path d="M640 0 L1140 0 L1140 880 L0 880 L0 700 C150 650 300 570 380 480 C470 380 520 150 640 0 Z" fill="url(#blueField)"/>
    <path d="M0 715 C160 660 310 585 390 495 C480 395 530 160 650 0" fill="none" stroke="#85cae6" stroke-width="3" opacity=".6"/>
  </svg>
  <div class="fold fold--one"></div>
  <div class="fold fold--two"></div>

  <!-- Left panel -->
  <div class="brand">
    <span class="brand__dot"></span>
    <span class="brand__name">Branton<br>Investigative Services</span>
  </div>
  <p class="brand__tagline">35 Years of Investigative Excellence!</p>
  <div class="art art--collage" role="img" aria-label="Collage photo: binary code, magnifier over cyber crime, eye scan and identity theft"></div>

  <p class="intro"><strong>Branton Investigative Services, LLC</strong> is a full service, private investigative agency that is licensed and bonded in the state of Oakridge. Located in central Oakridge we provide a complete array of investigative services. With 35 years of investigative and law enforcement experience we deliver professional results, ethically, confidentially, and with attention to detail.</p>

  <div class="art art--gavel" role="img" aria-label="Photo of a gold judge's gavel"></div>
  <div class="tab tab--contact"></div>
  <div class="badge badge--contact">Contact<br>Us</div>

  <address class="contact" style="font-style:normal">
    <p class="contact__phone">Phone: 555-318-0472</p>
    <p>Branton Investigative Services</p>
    <p>P.O. Box 40210</p>
    <p>Millbrook, Oakridge</p>
    <p>02917</p>
    <p>Email: CalBrantonPI@brantonpi.com</p>
    <p>Web: http://www.brantonpi.com</p>
  </address>

  <!-- Middle panel -->
  <div class="art art--binoculars" role="img" aria-label="Photo of binoculars with blue lenses"></div>
  <div class="art art--fraud" role="img" aria-label="Photo of a magnifier over the word fraud on a green target"></div>
  <div class="art art--scales" role="img" aria-label="Photo of gold scales of justice"></div>
  <div class="tab tab--about"></div>
  <div class="tab tab--services"></div>
  <div class="badge badge--services">Services</div>

  <ul class="services">
    <li class="indent"><svg class="tick" viewBox="0 0 14 14"><path d="M2 7 L5.5 11 L12 3" fill="none" stroke="#85cae6" stroke-width="2.4"/></svg>Attorney and law firm support</li>
    <li><svg class="tick" viewBox="0 0 14 14"><path d="M2 7 L5.5 11 L12 3" fill="none" stroke="#85cae6" stroke-width="2.4"/></svg>Pretrial and trial assistance</li>
    <li><svg class="tick" viewBox="0 0 14 14"><path d="M2 7 L5.5 11 L12 3" fill="none" stroke="#85cae6" stroke-width="2.4"/></svg>Background investigations</li>
    <li><svg class="tick" viewBox="0 0 14 14"><path d="M2 7 L5.5 11 L12 3" fill="none" stroke="#85cae6" stroke-width="2.4"/></svg>Missing persons and children</li>
    <li><svg class="tick" viewBox="0 0 14 14"><path d="M2 7 L5.5 11 L12 3" fill="none" stroke="#85cae6" stroke-width="2.4"/></svg>Corporate fraud</li>
    <li><svg class="tick" viewBox="0 0 14 14"><path d="M2 7 L5.5 11 L12 3" fill="none" stroke="#85cae6" stroke-width="2.4"/></svg>White collar crimes</li>
    <li><svg class="tick" viewBox="0 0 14 14"><path d="M2 7 L5.5 11 L12 3" fill="none" stroke="#85cae6" stroke-width="2.4"/></svg>Public and private corruption investigations</li>
    <li><svg class="tick" viewBox="0 0 14 14"><path d="M2 7 L5.5 11 L12 3" fill="none" stroke="#85cae6" stroke-width="2.4"/></svg>Individual private investigations</li>
    <li><svg class="tick" viewBox="0 0 14 14"><path d="M2 7 L5.5 11 L12 3" fill="none" stroke="#85cae6" stroke-width="2.4"/></svg>Insurance fraud</li>
    <li><svg class="tick" viewBox="0 0 14 14"><path d="M2 7 L5.5 11 L12 3" fill="none" stroke="#85cae6" stroke-width="2.4"/></svg>Motor vehicle accident reconstruction</li>
    <li><svg class="tick" viewBox="0 0 14 14"><path d="M2 7 L5.5 11 L12 3" fill="none" stroke="#85cae6" stroke-width="2.4"/></svg>Witness location and statements</li>
    <li><svg class="tick" viewBox="0 0 14 14"><path d="M2 7 L5.5 11 L12 3" fill="none" stroke="#85cae6" stroke-width="2.4"/></svg>Online computer crimes</li>
    <li><svg class="tick" viewBox="0 0 14 14"><path d="M2 7 L5.5 11 L12 3" fill="none" stroke="#85cae6" stroke-width="2.4"/></svg>Retail employee theft</li>
    <li><svg class="tick" viewBox="0 0 14 14"><path d="M2 7 L5.5 11 L12 3" fill="none" stroke="#85cae6" stroke-width="2.4"/></svg>Subpoena service</li>
    <li><svg class="tick" viewBox="0 0 14 14"><path d="M2 7 L5.5 11 L12 3" fill="none" stroke="#85cae6" stroke-width="2.4"/></svg>Skip tracing</li>
  </ul>

  <!-- Right panel -->
  <p class="about"><span class="about__spacer"></span>Cal Branton is the owner of Branton Investigative Services, LLC. He is a former law enforcement officer with 35 years of investigative and asset protection experience. He obtained the rank of Captain with the Oakridge State Patrol and Chief of Detectives with a county prosecutor's office during his law enforcement career.</p>
  <div class="badge badge--about">About<br>Us</div>

  <div class="tab tab--experience"></div>
  <div class="badge badge--experience">His<br>Experience</div>

  <ul class="experience">
    <li><span class="dot"></span>Special Projects/Auto Unit</li>
    <li><span class="dot"></span>Official Corruption Unit</li>
    <li><span class="dot"></span>High Technology Crimes and Investigative Support Unit (Unit Leader)</li>
    <li><span class="dot"></span>Special Investigations and Services Bureau (Bureau Chief)</li>
    <li><span class="dot"></span>Polygraph Unit</li>
    <li><span class="dot"></span>TRAK Unit (homicide tracking)</li>
    <li><span class="dot"></span>Special Investigations Unit (Backgrounds)</li>
    <li><span class="dot"></span>Brookvale Arena Grounds Unit</li>
    <li><span class="dot"></span>Alcohol Beverage Control Unit</li>
    <li><span class="dot"></span>Internal Affairs and Investigations Bureau (Bureau Chief)</li>
  </ul>
  <p class="more"><span>→</span> AND MANY MORE <span>←</span></p>
</main>
</body>
</html>
```